Velmora Publishing

I made a website myself www.velmorapublishing.co.uk a few years ago but I need a new design, which I will code. One that I can be proud of, that 's sexy, to win new customers and showcase my publishing skills. This is a publishing website so I want the home page and books page to be fantastic. I have a logo already so will like the same colour scheme or thereabouts. I have current files and features that I would like to add to your creativity and experience.

Target Market(s)

Web Designers, Graphic Designers

Industry/Entity Type

Book Publisher

Number of Pages Required

5+ page

Font styles to use
Sans Serif

Colors
0255a3
ffffff
ec1f27

Requirements
Must have
• Menu and Sub Menu
• Footer
• Buy Page - Shopping Cart
• Upload feature on the submissions page
• video section on home page (how we publish books)
• Ad space section
Nice to have
• social media bar
• Zoom in page

```html
<!DOCTYPE html>
<html lang="en">
<head>
<meta charset="utf-8">
<title>Velmora Publishing</title>
<link rel="stylesheet" href="https://fonts.googleapis.com/css2?family=Nunito+Sans:wght@300;400;600;700;800&display=swap">
<style>
:root{
  --blue:#0255a3;
  --red:#ec1f27;
  --green:#7cbb3a;
  --white:#ffffff;
  --ink:#333;
  --muted:#777;
  --partner:#444;
  --line:#c9c9c9;
  --paper:#efefef;
  --footer-top:#5b88b8;
  --footer-bottom:#1f4f8c;
}
*{box-sizing:border-box;margin:0;padding:0}
html,body{width:1200px;height:3066px;overflow:hidden}
body{font-family:"Nunito Sans",Arial,sans-serif;color:var(--ink);background:var(--white);position:relative}
section,header,footer{position:absolute;left:0;width:1200px}
/* header */
.site-header{top:0;height:94px;background:var(--white)}
.brand{position:absolute;left:180px;top:26px;display:flex;align-items:center;gap:12px}
.brand-dot{width:30px;height:30px;border-radius:50%;background:var(--red)}
.brand-name{font-size:26px;font-weight:800;color:var(--blue)}
.main-nav{position:absolute;left:492px;top:0;display:flex;height:94px}
.main-nav a{display:block;padding:38px 9px 0;height:94px;font-size:14.5px;color:#222;text-decoration:none;margin-right:4px}
.main-nav a.is-active{color:var(--red);border-bottom:3px solid var(--red)}
/* hero */
.hero{top:94px;height:509px}
.hero-photo{position:absolute;inset:0;background:linear-gradient(100deg,#c8a27c 0%,#b98e68 35%,#8b8a8a 60%,#d8d6d2 100%)}
.hero-shade{position:absolute;inset:0;background:rgba(0,0,0,.18)}
.hero-title{position:absolute;left:0;width:1200px;top:164px;text-align:center;color:var(--white);font-weight:700;font-size:42px;line-height:48px}
.btn-submit{position:absolute;left:515px;top:288px;width:172px;height:41px;background:var(--red);color:var(--white);font-size:15px;font-weight:700;text-align:center;line-height:41px}
.hero-dots{position:absolute;left:568px;top:465px;display:flex;gap:8px}
.hero-dots span{width:12px;height:12px;border-radius:50%;background:var(--white)}
.hero-dots span.is-current{background:transparent;border:2px solid var(--white)}
/* intro */
.intro{top:603px;height:517px;text-align:center}
.intro-title{position:absolute;left:0;top:50px;width:1200px;font-size:30px;line-height:32px;font-weight:700;color:var(--blue)}
.intro-text{position:absolute;left:190px;top:138px;width:820px;font-size:15px;line-height:29px;color:var(--muted)}
.feature{position:absolute;top:235px;width:232px;height:232px;border-radius:50%;color:var(--white);font-weight:700;font-size:17px}
.feature svg{position:absolute;left:76px;top:58px}
.feature span{position:absolute;left:0;width:232px;top:160px}
.feature--books{left:233px;background:var(--blue)}
.feature--authors{left:484px;background:var(--red)}
.feature--submissions{left:734px;background:var(--green)}
/* video */
.video{top:1120px;height:356px}
.video-still{position:absolute;inset:0;background:linear-gradient(180deg,#6e6f71 0%,#9a9b9d 45%,#5c5d60 100%)}
.video-label{position:absolute;left:242px;top:142px;font-size:35px;font-weight:300;color:var(--white);letter-spacing:1px}
.video-play{position:absolute;left:793px;top:101px}
/* steps */
.steps{top:1476px;height:660px;background:var(--paper)}
.section-title{position:absolute;left:0;width:1200px;text-align:center;font-size:27px;font-weight:600;color:#333}
.steps .section-title{top:48px}
.step{position:absolute;width:337px;height:192px;background:var(--white);border:1px solid var(--line);text-align:center;padding:0 30px}
.step h3{margin-top:52px;font-size:22px;font-weight:400;color:var(--blue)}
.step h3 b{color:var(--red);font-weight:700}
.step p{margin-top:8px;font-size:11.5px;line-height:19px;color:#555}
.step-icon{position:absolute;left:127px;top:-41px;width:82px;height:82px;border-radius:50%;border:2px solid var(--blue);background:var(--white)}
.step-icon svg{position:absolute;left:19px;top:19px}
.step--writing{left:227px;top:153px}
.step--submission{left:648px;top:153px}
.step--contract{left:227px;top:423px}
.step--review{left:648px;top:423px}
.step-links{position:absolute;left:0;top:0}
/* partners */
.partners{top:2136px;height:270px}
.partners .section-title{top:62px;font-weight:400;color:#777}
.partner{position:absolute;top:150px;font-size:26px;font-weight:700;color:var(--partner);white-space:nowrap;transform:translateX(-50%)}
/* testimonials */
.testimonials{top:2406px;height:298px;background:#f2f2f2}
.testimonials .section-title{top:44px;color:var(--red);font-weight:400;font-size:28px}
.author-photo{position:absolute;left:252px;top:86px;width:143px;height:143px;border-radius:50%;background:linear-gradient(160deg,#8a8f86,#c49a7f 55%,#5f6b58)}
.quote{position:absolute;left:412px;top:116px;width:500px;font-size:15.5px;line-height:31px;color:#555}
.quote-mark{font-size:34px;color:#555;font-family:Georgia,serif;line-height:0}
.quote-by{position:absolute;left:430px;top:195px;font-size:13.5px;color:#555}
/* footer */
.site-footer{top:2704px;height:362px;background:linear-gradient(180deg,var(--footer-top),var(--footer-bottom))}
.footer-brand{position:absolute;left:186px;top:160px;width:180px;text-align:center;font-size:26px;line-height:28px;font-weight:700;color:rgba(255,255,255,.35)}
.footer-col{position:absolute;top:66px;color:var(--white)}
.footer-col h4{font-size:19px;font-weight:400;margin-bottom:10px}
.footer-col a{display:block;font-size:13.5px;line-height:30.5px;color:var(--white);text-decoration:none}
.social{display:flex;gap:6px;margin-top:4px}
.social span{width:27px;height:27px;border-radius:50%;border:2px solid var(--white)}
.copyright{position:absolute;left:0;top:321px;width:1200px;text-align:center;font-size:10.5px;color:rgba(255,255,255,.7)}
</style>
</head>
<body>

<header class="site-header">
  <div class="brand"><span class="brand-dot"></span><span class="brand-name">Velmora Publishing</span></div>
  <nav class="main-nav">
    <a href="#" class="is-active">Home</a>
    <a href="#">Publishing</a>
    <a href="#">Submissions</a>
    <a href="#">Books</a>
    <a href="#">Authors</a>
    <a href="#">Seminars</a>
    <a href="#">Contact</a>
  </nav>
</header>

<section class="hero">
  <div class="hero-photo" role="img" aria-label="Smiling woman reading beside an open book on a table"></div>
  <div class="hero-shade"></div>
  <h1 class="hero-title">Velmora Publishing<br>Self-Publishing That Works</h1>
  <a class="btn-submit">SUBMIT BOOK</a>
  <div class="hero-dots"><span class="is-current"></span><span></span><span></span><span></span></div>
</section>

<section class="intro">
  <h2 class="intro-title">Have a story to tell?<br>We can help you publish your book.</h2>
  <p class="intro-text">Welcome to Velmora Publishing, we are an independent publishing company located in London/Surrey. We publish Trade (fiction and non-fiction), &amp; Young Adult (YA) in a variety of subjects</p>
  <div class="feature feature--books">
    <svg width="80" height="70" viewBox="0 0 80 70" fill="none" stroke="#fff" stroke-width="5" stroke-linejoin="round">
      <path d="M40 14 C30 6 16 6 6 10 V60 C16 56 30 56 40 64 C50 56 64 56 74 60 V10 C64 6 50 6 40 14 Z"/>
      <path d="M40 14 V64"/>
    </svg>
    <span>BOOKS</span>
  </div>
  <div class="feature feature--authors">
    <svg width="80" height="80" viewBox="0 0 80 80" fill="none" stroke="#fff" stroke-width="4" stroke-linecap="round">
      <circle cx="56" cy="22" r="14"/>
      <path d="M46 32 L14 66 L20 72 L52 40"/>
      <path d="M10 74 H40"/>
    </svg>
    <span>AUTHORS</span>
  </div>
  <div class="feature feature--submissions">
    <svg width="80" height="80" viewBox="0 0 80 80" fill="#fff">
      <rect x="26" y="8" width="28" height="30"/>
      <rect x="6" y="36" width="68" height="8"/>
      <rect x="8" y="48" width="64" height="28"/>
    </svg>
    <span>SUBMISSIONS</span>
  </div>
</section>

<section class="video">
  <div class="video-still" role="img" aria-label="Stacks of printed books moving along factory rollers"></div>
  <div class="video-label">Learn How We Publish Books</div>
  <svg class="video-play" width="124" height="124" viewBox="0 0 124 124">
    <circle cx="62" cy="62" r="60" fill="#111"/>
    <circle cx="62" cy="62" r="50" fill="#fff"/>
    <path d="M50 40 L82 62 L50 84 Z" fill="#111"/>
  </svg>
</section>

<section class="steps">
  <h2 class="section-title">Publish Your Book in 4 Easy Steps</h2>
  <svg class="step-links" width="1200" height="660" viewBox="0 0 1200 660" fill="none" stroke="#999" stroke-width="2">
    <path d="M583 249 H631 M621 240 L631 249 L621 258"/>
    <path d="M816 345 V382 M807 372 L816 382 L825 372"/>
    <path d="M583 525 H631 M621 516 L631 525 L621 534"/>
  </svg>
  <div class="step step--writing">
    <div class="step-icon"><svg width="44" height="44" viewBox="0 0 44 44" fill="none" stroke="#ec1f27" stroke-width="3" stroke-linejoin="round"><path d="M8 36 L12 26 L32 6 L38 12 L18 32 Z"/><path d="M28 10 L34 16"/></svg></div>
    <h3><b>1.</b>Writing</h3>
    <p>You write a book to the best of your ability And after redrafting several times when you honestly feel that you have done the best you Possibly can with it, you send it to us</p>
  </div>
  <div class="step step--submission">
    <div class="step-icon"><svg width="44" height="44" viewBox="0 0 44 44" fill="none" stroke="#ec1f27" stroke-width="3"><rect x="14" y="4" width="16" height="16"/><rect x="4" y="20" width="36" height="6"/><rect x="6" y="26" width="32" height="14"/></svg></div>
    <h3><b>2.</b>Submission</h3>
    <p>If your book is in our subject matter and you think you have something that could tickle our fancy, send Us your book for review.</p>
  </div>
  <div class="step step--contract">
    <div class="step-icon"><svg width="44" height="44" viewBox="0 0 44 44" fill="none" stroke="#ec1f27" stroke-width="3"><path d="M10 4 H28 L36 12 V40 H10 Z"/><path d="M16 18 H30 M16 25 H30 M16 32 H30"/></svg></div>
    <h3><b>4.</b>Contract</h3>
    <p>You send us your book and our editorial team will look over it and decide if we like it and then we will Decide what</p>
  </div>
  <div class="step step--review">
    <div class="step-icon"><svg width="44" height="44" viewBox="0 0 44 44" fill="none" stroke="#ec1f27" stroke-width="3"><rect x="6" y="6" width="26" height="34"/><path d="M11 16 L14 19 L19 13 M11 28 L14 31 L19 25 M22 17 H28 M22 29 H28"/><path d="M30 24 L40 10"/></svg></div>
    <h3><b>3.</b>Review</h3>
    <p>You send us your book and our editorial team will look over it and decide if we like it and</p>
  </div>
</section>

<section class="partners">
  <h2 class="section-title">Companies We Work With</h2>
  <div class="partner" style="left:243px">Orvane</div>
  <div class="partner" style="left:378px">Pelio</div>
  <div class="partner" style="left:519px">Tessary</div>
  <div class="partner" style="left:664px">Quillon</div>
  <div class="partner" style="left:809px">Harrow &amp; Finch</div>
  <div class="partner" style="left:959px">Brindle</div>
</section>

<section class="testimonials">
  <h2 class="section-title">Testimonials</h2>
  <div class="author-photo" role="img" aria-label="Portrait of the quoted author"></div>
  <p class="quote"><span class="quote-mark">“</span> You send us your book and our editorial team will look over it and decide if we like it and then we will Decide what. <span class="quote-mark">”</span></p>
  <p class="quote-by">By Author Name</p>
</section>

<footer class="site-footer">
  <div class="footer-brand">Velmora<br>Publishing</div>
  <div class="footer-col" style="left:425px"><h4>Quick Links</h4><a href="#">Submissions</a><a href="#">Production</a><a href="#">Ebook</a></div>
  <div class="footer-col" style="left:585px"><h4>Resources</h4><a href="#">Books</a><a href="#">Seminars</a><a href="#">Packages</a></div>
  <div class="footer-col" style="left:740px"><h4>Sublinks</h4><a href="#">Authors</a><a href="#">Contact</a><a href="#">Careers</a></div>
  <div class="footer-col" style="left:901px"><h4>Follow Us</h4><div class="social"><span></span><span></span><span></span><span></span></div></div>
  <p class="copyright">© 2016 Company Name. All right reserved. Term of Use</p>
</footer>

</body>
</html>
```